Brightlane Rapid Rinse Web Design

We are looking for a web design that highlights our state of the art fully automated commercial vehicle washing equipment. Similar system to a car wash however this system is meant for the largest vehicles on our roadways. Transport trucks with or without a trailer, busses both highway and school, RV's from 5th wheel type to A Class. Cement trucks, dump trucks, vac trucks, fuel trucks etc. Pick ups with utility trailers...Refrigerator truck clean outs.
Brightlane Rapid Rinse will wash your vehicle quickly and with a minimal impact on the environment

Home page
About us
Why Brightlane
Services and pricing
Videos of wash system
Fleets
contact us

Target Market(s)

Commercial vehicle owners and operators as well as corporate fleets. Includes busses, municipal, school and highway.both school and

Industry/Entity Type

transportation

Coding

Coded - Design and coding required

Number of Pages Required

5+ page

Font styles to use
Sans Serif

Colors
0054AA
0677BA
7BADD7
CADEEF
E8F1F8

Requirements
Must have
• Welcome page,why us page which describes the financial and environmental benefits. payment processing page, contact us page, Services which is washing vehicles and greasing for commercial vehicles that want that service and grease
Nice to have
• pictures of both clean and dirty commercial vehicles ie. before and after

```html
<!DOCTYPE html>
<html lang="en">
<head>
<meta charset="utf-8">
<title>Brightlane Rapid Rinse</title>
<link href="https://fonts.googleapis.com/css2?family=Poppins:wght@400;500;600&family=Rubik:wght@500;600;700&display=swap" rel="stylesheet">
<style>
:root{
  --blue-deep:#0054AA;
  --blue:#0677BA;
  --blue-mid:#7BADD7;
  --blue-pale:#CADEEF;
  --blue-mist:#E8F1F8;
  --navy:#0c3f6e;
  --ink:#1b1b1b;
  --footer:#202428;
  --white:#ffffff;
}
*{box-sizing:border-box;margin:0;padding:0}
html,body{width:1200px;height:4329px;overflow:hidden}
body{font-family:"Poppins",sans-serif;color:var(--ink);background:var(--white);position:relative}
.abs{position:absolute}
h2.section-title{font-family:"Rubik",sans-serif;font-weight:700;font-size:36px;text-align:center;position:absolute;left:0;width:1200px;letter-spacing:-.3px}
.underline{position:absolute;height:5px;width:84px;background:var(--blue);left:558px}
.btn{display:inline-flex;align-items:center;gap:12px;border-radius:30px;background:var(--blue);color:#fff;font-size:15px;padding:0 12px 0 18px;height:40px;border:2px solid #fff;position:absolute;white-space:nowrap}
.btn .dot{width:17px;height:17px;border-radius:50%;background:#fff;display:inline-flex;align-items:center;justify-content:center}
/* header */
.site-header{left:0;top:0;width:1200px;height:87px;background:linear-gradient(90deg,#0d3866,#0e4478 60%,#0d3866);z-index:3}
.brand{left:22px;top:30px;color:#fff;font-family:"Poppins",sans-serif;font-weight:600;font-size:18px;line-height:1.2;white-space:nowrap}
.nav{left:260px;top:30px;display:flex;gap:44px;color:#fff;font-size:17px;font-weight:500}
.nav .active{position:relative}
.nav .active:before{content:"";position:absolute;left:50%;top:-9px;width:6px;height:6px;border-radius:50%;background:#fff;transform:translateX(-50%)}
.call{left:950px;top:0;width:250px;height:87px;background:#fff}
.call-inner{left:950px;top:0;width:250px;height:78px;background:var(--blue-deep);border-bottom-left-radius:20px;color:#fff}
.call-inner .circle{position:absolute;left:14px;top:24px;width:36px;height:36px;border-radius:50%;background:#fff;display:flex;align-items:center;justify-content:center}
.call-inner .lbl{position:absolute;left:56px;top:13px;font-size:16px}
.call-inner .num{position:absolute;left:56px;top:36px;font-size:25px;font-weight:600}
/* hero */
.hero{left:0;top:0;width:1200px;height:667px;background:radial-gradient(ellipse at 55% 45%,#c98a2a 0%,#9a5e1c 35%,#3b2b1e 75%,#1e1a16 100%)}
.hero-title{left:0;top:212px;width:1200px;text-align:center;color:#fff;font-family:"Rubik",sans-serif;font-weight:700;font-size:58px;line-height:1.17}
.slider-dots{left:46px;top:322px}
.slider-dots span{display:block;width:13px;height:13px;border-radius:50%;border:2px solid #fff;margin-bottom:8px}
.slider-dots span.on{background:var(--blue);border-color:var(--blue)}
.social-rail{left:1138px;top:196px;width:30px}
.social-rail .ico{margin-bottom:16px}
.ico{display:flex;width:30px;height:30px;border-radius:50%;background:#fff;align-items:center;justify-content:center}
.rail-line{left:1152px;top:405px;width:2px;height:90px;background:#fff}
.scroll{left:1140px;top:500px;color:#fff;font-size:14px;writing-mode:vertical-rl}
/* mission */
.mission-outer{left:110px;top:587px;width:979px;height:240px;background:#fff;border-radius:30px}
.mission{left:123px;top:600px;width:953px;height:212px;background:var(--blue);border-radius:24px;color:#fff;text-align:center}
.mission h3{font-family:"Rubik",sans-serif;font-weight:600;font-size:34px;margin-top:24px}
.mission p{font-size:20px;line-height:1.58;width:600px;margin:16px auto 0}
/* about */
.about-title{left:125px;top:1012px;font-family:"Rubik",sans-serif;font-weight:700;font-size:36px}
.about-line{left:125px;top:1060px;width:82px;height:5px;background:var(--blue)}
.about-text{left:125px;top:1085px;width:474px;font-size:14px;line-height:1.77;color:#222}
.about-accent{left:938px;top:904px;width:166px;height:146px;background:#3b8bcc}
.about-photo{left:640px;top:921px;width:447px;height:494px;background:linear-gradient(90deg,#c9cdd0,#e5e7e8 40%,#b3b8bc);box-shadow:0 6px 18px rgba(0,0,0,.2)}
/* services */
.services{left:0;top:1501px;width:1200px;height:675px;background:var(--blue-mist)}
.svc{top:1671px;width:299px;height:420px;background:#fff;box-shadow:0 4px 12px rgba(0,0,0,.22)}
.svc .photo{position:absolute;left:0;top:0;width:100%;height:348px}
.svc .label{position:absolute;left:0;bottom:0;width:100%;height:72px;background:var(--blue);color:#fff;font-size:24px;font-weight:500;display:flex;align-items:center;justify-content:center}
.svc-featured{background:linear-gradient(180deg,#4a2f34,#5c4a4d 50%,#6c6566)}
.svc-featured .overlay{position:absolute;inset:0;background:rgba(20,20,25,.55)}
.svc-featured h4{position:absolute;left:30px;top:85px;color:#fff;font-size:20px;font-weight:500}
.svc-featured p{position:absolute;left:30px;top:133px;width:240px;color:#fff;font-size:14px;line-height:1.7;text-align:justify}
.svc-featured .more{position:absolute;left:27px;top:340px;width:245px;height:60px;background:var(--blue);color:#fff;font-size:20px;display:flex;align-items:center;justify-content:center}
/* pricing */
.pricing{left:0;top:2176px;width:1200px;height:664px;background:linear-gradient(180deg,#0a6cb0,var(--blue) 40%,#1077bb)}
.price-card{top:2366px;width:373px;height:326px;background:#fff;border-radius:6px;overflow:hidden;box-shadow:0 6px 16px rgba(0,0,0,.25);text-align:center}
.price-card .head{height:165px;background:var(--navy);color:#fff;padding-top:24px}
.price-card .head .sub{font-size:22px;font-weight:500}
.price-card .head .name{font-family:"Rubik",sans-serif;font-weight:700;font-size:38px;line-height:1.12;margin-top:8px}
.price-card .plabel{font-size:21px;margin-top:22px}
.price-card .amount{font-family:"Rubik",sans-serif;font-weight:600;font-size:60px;margin-top:2px}
.price-card .amount small{font-size:34px}
.pdots{left:572px;top:2744px;display:flex;gap:8px}
.pdots span{width:13px;height:13px;border-radius:50%;border:2px solid #fff}
.pdots span.on{background:#fff}
/* gallery */
.tile{top:3013px;width:207px;height:189px;box-shadow:0 4px 10px rgba(0,0,0,.3)}
.arrow{top:3078px;width:58px;height:58px;border-radius:50%;background:#111;border:3px solid #fff;display:flex;align-items:center;justify-content:center}
.play{left:574px;top:3080px;width:54px;height:54px;border-radius:50%;background:#fff;display:flex;align-items:center;justify-content:center}
/* contact */
.contact-bg{left:0;top:3294px;width:1200px;height:617px;background:linear-gradient(180deg,#fff 0%,#f1f3f4 25%,#d8dadc 70%,#c6c8ca 100%)}
.contact-sub{left:375px;top:3451px;width:450px;text-align:center;font-size:16px;line-height:1.45;color:#222}
.field{background:#1b1b1b;color:#ddd;font-size:12.5px;padding:10px 18px}
/* footer */
.footer{left:0;top:3911px;width:1200px;height:418px;background:var(--footer);color:#fff}
.foot-brand{left:140px;top:4052px;width:300px;color:var(--blue);font-family:"Poppins",sans-serif;font-weight:600;font-size:24px;line-height:1.2;text-align:center;white-space:nowrap}
.foot-social{left:168px;top:4130px;display:flex;gap:20px}
.fcol h5{font-family:"Rubik",sans-serif;font-weight:600;font-size:19px}
.fcol .bar{width:48px;height:3px;background:var(--blue);margin:14px 0 12px}
.fcol ul{list-style:none;font-size:12.5px;line-height:2}
.fcontact{left:824px;top:4050px;font-size:12.5px;line-height:1.4}
.fcontact .row{display:flex;gap:16px;margin-bottom:18px}
.fcontact .ic{width:32px;height:32px;border-radius:50%;background:#1e5b8e;display:flex;align-items:center;justify-content:center;flex:none}
.fcontact .k{color:#aaa;font-size:12px}
.fdivider{left:110px;top:4249px;width:980px;height:1px;background:#2f6aa0}
.copy{left:0;top:4280px;width:1200px;text-align:center;font-size:13px}
</style>
</head>
<body>

<!-- hero -->
<div class="abs hero" role="img" aria-label="Orange transport truck inside a wash bay"></div>
<div class="abs hero-title">BRIGHTLANE<br>RAPID RINSE</div>
<a class="btn" style="left:355px;top:358px">Book a Wash <span class="dot"><svg width="9" height="9" viewBox="0 0 10 10"><path d="M3 1l4 4-4 4" stroke="#0677BA" stroke-width="2" fill="none"/></svg></span></a>
<a class="btn" style="left:525px;top:358px">Learn More <span class="dot"><svg width="9" height="9" viewBox="0 0 10 10"><path d="M3 1l4 4-4 4" stroke="#0677BA" stroke-width="2" fill="none"/></svg></span></a>
<a class="btn" style="left:695px;top:358px">Contact Us <span class="dot" style="margin-left:14px"><svg width="9" height="9" viewBox="0 0 10 10"><path d="M3 1l4 4-4 4" stroke="#0677BA" stroke-width="2" fill="none"/></svg></span></a>
<div class="abs slider-dots"><span></span><span class="on"></span><span></span></div>
<div class="abs social-rail">
  <span class="ico" aria-label="Share"><svg width="14" height="14" viewBox="0 0 14 14"><circle cx="3" cy="7" r="2" fill="#0677BA"/><circle cx="11" cy="3" r="2" fill="#0677BA"/><circle cx="11" cy="11" r="2" fill="#0677BA"/><path d="M3 7L11 3M3 7l8 4" stroke="#0677BA" stroke-width="1.3"/></svg></span>
  <span class="ico" aria-label="Video"><svg width="12" height="12" viewBox="0 0 12 12"><path d="M3 1l8 5-8 5z" fill="#0677BA"/></svg></span>
  <span class="ico" aria-label="Chat"><svg width="14" height="13" viewBox="0 0 14 13"><path d="M1 1h12v8H5l-3 3V9H1z" fill="#0677BA"/></svg></span>
  <span class="ico" aria-label="Link"><svg width="14" height="14" viewBox="0 0 14 14"><rect x="1" y="4" width="7" height="6" rx="3" stroke="#0677BA" stroke-width="1.6" fill="none"/><rect x="6" y="4" width="7" height="6" rx="3" stroke="#0677BA" stroke-width="1.6" fill="none"/></svg></span>
  <span class="ico" aria-label="Email"><svg width="14" height="11" viewBox="0 0 16 12"><rect width="16" height="12" rx="1" fill="#0677BA"/><path d="M1 1l7 5 7-5" stroke="#fff" stroke-width="1.5" fill="none"/></svg></span>
</div>
<div class="abs rail-line"></div>
<div class="abs scroll">Scroll Down</div>

<!-- header -->
<header class="abs site-header">
  <div class="abs brand">Brightlane Rapid Rinse</div>
  <nav class="abs nav"><span class="active">Home</span><span>About</span><span>Why Us</span><span>Services and pricing</span><span>Videos</span><span>Fleets</span></nav>
</header>
<div class="abs call" style="z-index:3"></div>
<div class="abs call-inner" style="z-index:4">
  <span class="circle"><svg width="18" height="18" viewBox="0 0 24 24"><path d="M6.6 10.8a15 15 0 006.6 6.6l2.2-2.2c.3-.3.7-.4 1-.2 1.1.4 2.3.6 3.6.6.6 0 1 .4 1 1V20c0 .6-.4 1-1 1A17 17 0 013 4c0-.6.4-1 1-1h3.5c.6 0 1 .4 1 1 0 1.3.2 2.5.6 3.6.1.3 0 .7-.2 1z" fill="#0054AA"/></svg></span>
  <span class="lbl">Call Us</span>
  <span class="num">555-014-2200</span>
</div>

<!-- mission -->
<div class="abs mission-outer"></div>
<section class="abs mission">
  <h3>Our Mission</h3>
  <p>A concise statement about our dedication to revolutionizing truck washing with advanced technology and sustainable practices, set against a dark blue backdrop.</p>
</section>

<!-- about -->
<h2 class="abs about-title">ABOUT US</h2>
<div class="abs about-line"></div>
<p class="abs about-text">Saerspiciatis undeasepoiise oklasdo mnis aidaste natus error sit voluptatem accusan tium doloremque laudantium, totam rem aperiam, ease aque ipaefdsa quae ab illo inventore veritatis ease quasi architecto beatae vitae dicta sunt explicabo. Nemo enim ipsam voluptatem quia volasdfupta sde sessitasese aspernatur autodit aut fugitsdsed quisaea consequuntur magni dolores eos qui ratione voluptatem sequi nesciunt.</p>
<a class="btn" style="left:125px;top:1292px;border-color:var(--blue-deep);box-shadow:0 0 0 2px #0054AA">Learn More <span class="dot" style="margin-left:22px"><svg width="9" height="9" viewBox="0 0 10 10"><path d="M3 1l4 4-4 4" stroke="#0677BA" stroke-width="2" fill="none"/></svg></span></a>
<div class="abs about-accent"></div>
<div class="abs about-photo" role="img" aria-label="Striped rotating wash brush beside a white box truck"></div>

<!-- services -->
<section class="abs services"></section>
<h2 class="section-title" style="top:1580px">SERVICES</h2>
<div class="underline" style="top:1632px"></div>
<div class="abs svc svc-featured" style="left:113px" role="img" aria-label="Truck passing through red brushes in a wash tunnel">
  <div class="overlay"></div>
  <h4>Automated Truck Wash:</h4>
  <p>A section to describe our core service, emphasizing speed and efficiency. Use a layout with dark blue headings and clear bullet points.</p>
  <div class="more">Learn More</div>
</div>
<div class="abs svc" style="left:450px">
  <div class="photo" role="img" aria-label="Blue dump truck being rinsed" style="background:linear-gradient(180deg,#8c9aa4,#4e6478 55%,#5d6266)"></div>
  <div class="label">Additional Services</div>
</div>
<div class="abs svc" style="left:788px">
  <div class="photo" role="img" aria-label="Fleet truck inside a wash bay with coloured brushes" style="background:linear-gradient(90deg,#6e6a70,#c5c6c8 50%,#6e6a70)"></div>
  <div class="label">Fleet Services</div>
</div>

<!-- pricing -->
<section class="abs pricing" role="img" aria-label="Blue-tinted photo of trucks in a wash bay"></section>
<h2 class="section-title" style="top:2252px;color:#fff">PRICING AND PACKAGES</h2>
<div class="underline" style="top:2304px;background:#fff"></div>
<div class="abs price-card" style="left:190px">
  <div class="head"><div class="sub">Uaselkalsem Caseliiase</div><div class="name">Kcasei Caserq<br>Uasenm</div></div>
  <div class="plabel">Price</div>
  <div class="amount">200.00 <small>US $</small></div>
</div>
<div class="abs price-card" style="left:622px">
  <div class="head"><div class="sub">Uaselkalsem Caseliiase</div><div class="name">Kcasei Caserq<br>Uasenm</div></div>
  <div class="plabel">Price</div>
  <div class="amount">200.00 <small>US $</small></div>
</div>
<div class="abs pdots"><span></span><span class="on"></span><span></span></div>

<!-- gallery -->
<h2 class="section-title" style="top:2916px">GALLERY AND VIDEOS</h2>
<div class="underline" style="top:2968px"></div>
<div class="abs tile" style="left:-160px;background:linear-gradient(90deg,#9ca2a6,#d5d8da)" role="img" aria-label="Truck in wash bay"></div>
<div class="abs tile" style="left:50px;background:linear-gradient(90deg,#c9cbce,#8f3a32 50%,#d4d6d8)" role="img" aria-label="Red trucks being washed"></div>
<div class="abs tile" style="left:274px;background:linear-gradient(90deg,#d18a2a,#5a4a36 70%)" role="img" aria-label="Orange truck with trailer"></div>
<div class="abs tile" style="left:497px;background:linear-gradient(90deg,#3b3f44,#6d7479 60%,#b9bdc0)" role="img" aria-label="Wash system video preview"></div>
<div class="abs tile" style="left:719px;background:linear-gradient(90deg,#c5c8ca,#9c2b2e 55%,#303236)" role="img" aria-label="Red and black wash brushes"></div>
<div class="abs tile" style="left:943px;background:linear-gradient(90deg,#c2c5c7,#eceeef 50%,#8a8f93)" role="img" aria-label="White trucks in wash bay"></div>
<div class="abs tile" style="left:1165px;background:linear-gradient(90deg,#5f656a,#a0a5a8)" role="img" aria-label="Truck in wash bay"></div>
<div class="abs play"><svg width="20" height="22" viewBox="0 0 20 22"><path d="M3 1l16 10-16 10z" fill="#0677BA"/></svg></div>
<div class="abs arrow" style="left:16px"><svg width="16" height="16" viewBox="0 0 16 16"><path d="M11 2L5 8l6 6" stroke="#fff" stroke-width="2.5" fill="none"/></svg></div>
<div class="abs arrow" style="left:1124px"><svg width="16" height="16" viewBox="0 0 16 16"><path d="M5 2l6 6-6 6" stroke="#fff" stroke-width="2.5" fill="none"/></svg></div>

<!-- contact -->
<div class="abs contact-bg" role="img" aria-label="Faded wash tunnel interior"></div>
<h2 class="section-title" style="top:3373px">CONTACT US</h2>
<div class="underline" style="top:3425px"></div>
<p class="abs contact-sub">Saers lkses sepiciatis unde omnis voluptatem asccusan tium doloremque.</p>
<div class="abs field" style="left:294px;top:3529px;width:624px;height:38px">Your Name *</div>
<div class="abs field" style="left:294px;top:3590px;width:301px;height:38px">Email *</div>
<div class="abs field" style="left:617px;top:3590px;width:301px;height:38px">Phone Number *</div>
<div class="abs field" style="left:294px;top:3649px;width:624px;height:121px">Enter Your Message *</div>
<a class="btn" style="left:517px;top:3793px;border-color:#fff">Send Message <span class="dot"><svg width="9" height="9" viewBox="0 0 10 10"><path d="M3 1l4 4-4 4" stroke="#0677BA" stroke-width="2" fill="none"/></svg></span></a>

<!-- footer -->
<footer class="abs footer"></footer>
<div class="abs foot-brand">Brightlane Rapid Rinse</div>
<div class="abs foot-social">
  <span class="ico" aria-label="Share"><svg width="14" height="14" viewBox="0 0 14 14"><circle cx="3" cy="7" r="2" fill="#0054AA"/><circle cx="11" cy="3" r="2" fill="#0054AA"/><circle cx="11" cy="11" r="2" fill="#0054AA"/><path d="M3 7L11 3M3 7l8 4" stroke="#0054AA" stroke-width="1.3"/></svg></span>
  <span class="ico" aria-label="Chat"><svg width="14" height="13" viewBox="0 0 14 13"><path d="M1 1h12v8H5l-3 3V9H1z" fill="#0054AA"/></svg></span>
  <span class="ico" aria-label="Video"><svg width="12" height="12" viewBox="0 0 12 12"><path d="M3 1l8 5-8 5z" fill="#0054AA"/></svg></span>
  <span class="ico" aria-label="Link"><svg width="14" height="14" viewBox="0 0 14 14"><rect x="1" y="4" width="7" height="6" rx="3" stroke="#0054AA" stroke-width="1.6" fill="none"/><rect x="6" y="4" width="7" height="6" rx="3" stroke="#0054AA" stroke-width="1.6" fill="none"/></svg></span>
  <span class="ico" aria-label="Email"><svg width="14" height="11" viewBox="0 0 16 12"><rect width="16" height="12" rx="1" fill="#0054AA"/><path d="M1 1l7 5 7-5" stroke="#fff" stroke-width="1.5" fill="none"/></svg></span>
</div>
<div class="abs fcol" style="left:467px;top:3996px;color:#fff">
  <h5>Quick Links</h5><div class="bar"></div>
  <ul><li>Home</li><li>About</li><li>Why Us</li><li>Services and pricing</li><li>Videos</li><li>Fleets</li></ul>
</div>
<div class="abs fcol" style="left:655px;top:3996px;color:#fff">
  <h5>Links</h5><div class="bar"></div>
  <ul><li>Copyright</li><li>Terms of Use</li><li>Privacy Policy</li><li>Accessibility</li><li>Sitemap</li><li>Contact Us</li></ul>
</div>
<div class="abs fcol" style="left:824px;top:3996px;color:#fff"><h5>Contact US</h5><div class="bar"></div></div>
<div class="abs fcontact" style="color:#fff">
  <div class="row"><span class="ic"><svg width="14" height="16" viewBox="0 0 14 18"><path d="M7 0a7 7 0 017 7c0 5-7 11-7 11S0 12 0 7a7 7 0 017-7z" fill="#0677BA"/><circle cx="7" cy="7" r="2.5" fill="#1e5b8e"/></svg></span><div><div class="k">Address</div>42 Harbor Line Rd, Westvale<br>Toronto, Canada, 10234</div></div>
  <div class="row"><span class="ic"><svg width="14" height="14" viewBox="0 0 24 24"><path d="M6.6 10.8a15 15 0 006.6 6.6l2.2-2.2c.3-.3.7-.4 1-.2 1.1.4 2.3.6 3.6.6.6 0 1 .4 1 1V20c0 .6-.4 1-1 1A17 17 0 013 4c0-.6.4-1 1-1h3.5c.6 0 1 .4 1 1 0 1.3.2 2.5.6 3.6.1.3 0 .7-.2 1z" fill="#0677BA"/></svg></span><div><div class="k">Call Us</div>+1 555 014 2200</div></div>
  <div class="row"><span class="ic"><svg width="14" height="11" viewBox="0 0 16 12"><rect width="16" height="12" rx="1" fill="#0677BA"/><path d="M1 1l7 5 7-5" stroke="#1e5b8e" stroke-width="1.5" fill="none"/></svg></span><div><div class="k">Email</div>info@brightlanerinse.com</div></div>
</div>
<div class="abs fdivider"></div>
<div class="abs copy" style="color:#fff">©2024. All rights reserved.</div>

</body>
</html>
```